Business card for builder specialising in renovations.

Need a card for our building business. Business name is under Martin Powles.
Have licence number on card ( 527691K)
Contact number (0400 382 415)
Want to work on logo for some business cards and shirts - something with MP or MPB or open to ideas??
No animations, No hammers. Something sharp and eye catching.
Highlight that we are a renovation specialist. Simple on front with extra details on back with some lines to jot down things.

Target Market(s)

Renovators

Industry/Entity Type

Building

Contact Information for Business Card

2 sided with room on back to jot things down.
Extra details on back so front can be simple ..like, renovations, bathrooms, decks, extensions, new builds,

Logo Text

MP

Font styles to use
Serif

Requirements
Must have
• Eye catching design .
• Name : Martin powles
• Licence number
• Contact number - 0400382415
Nice to have
• Some logo design that we can carry through to other forms of advertising
• Local builder
• Quality work
Should not have
• No animations

```html
<!DOCTYPE html>
<html lang="en">
<head>
<meta charset="utf-8">
<title>Martin Powles – Business Card</title>
<link rel="stylesheet" href="https://fonts.googleapis.com/css2?family=Tinos:wght@400;700&display=swap">
<style>
  :root {
    --stage: #2b2b2b;
    --card-black: #000000;
    --brand-blue: #1a78c2;
    --paper-white: #ffffff;
    --ink-white: #f2f2f2;
  }
  * { box-sizing: border-box; margin: 0; padding: 0; }
  html, body { width: 1200px; height: 900px; overflow: hidden; }
  body {
    background: var(--stage);
    font-family: "Tinos", "Times New Roman", serif;
    position: relative;
  }
  .card {
    position: absolute;
    width: 700px;
    height: 400px;
    background: var(--card-black);
    overflow: hidden;
    box-shadow: 0 14px 30px rgba(0,0,0,.55);
  }

  /* Back of card */
  .card--back { left: 70px; top: 70px; }
  .brand-lockup {
    position: absolute;
    top: 92px; left: 0; right: 0;
    display: flex; align-items: center; justify-content: center; gap: 18px;
  }
  .brand-lockup__square {
    width: 54px; height: 54px;
    border: 4px solid var(--brand-blue);
  }
  .brand-lockup__name {
    color: var(--brand-blue);
    font-size: 44px;
    letter-spacing: 2px;
  }
  .back-web {
    position: absolute;
    top: 218px; left: 0; right: 0;
    text-align: center;
    color: var(--ink-white);
    font-size: 22px;
  }
  .back-web .accent { color: var(--brand-blue); }
  .services-pill {
    position: absolute;
    top: 262px; left: 40px; right: 40px;
    border: 2px solid var(--brand-blue);
    border-radius: 16px;
    padding: 5px 0;
    text-align: center;
    color: var(--ink-white);
    font-size: 19px;
    letter-spacing: .5px;
  }

  /* Front of card */
  .card--front { left: 430px; top: 440px; }
  .monogram-panel {
    position: absolute;
    left: 0; top: 0;
    width: 380px; height: 400px;
    background: var(--paper-white);
    border: 12px solid var(--brand-blue);
    display: flex; align-items: center; justify-content: center;
  }
  .monogram-panel__text {
    color: var(--brand-blue);
    font-size: 150px;
    font-weight: 700;
    line-height: 1;
  }
  .contact {
    position: absolute;
    right: 28px; top: 34px;
    text-align: right;
    color: var(--ink-white);
    font-size: 17px;
    line-height: 1.45;
  }
  .contact__name {
    color: var(--brand-blue);
    font-size: 28px;
    letter-spacing: 1px;
    line-height: 1.1;
  }
  .contact__role { font-size: 17px; margin-bottom: 4px; }
  .contact .label, .contact .accent { color: var(--brand-blue); }
  .contact__row { display: flex; justify-content: flex-end; align-items: center; gap: 8px; }
  .contact__icon { width: 14px; height: 14px; fill: var(--ink-white); flex: none; }
</style>
</head>
<body>

  <section class="card card--back" aria-label="Card back">
    <div class="brand-lockup">
      <span class="brand-lockup__square"></span>
      <span class="brand-lockup__name">MARTIN POWLES</span>
    </div>
    <p class="back-web">www.<span class="accent">martinpowles</span>.com</p>
    <p class="services-pill">RENOVATIONS, BATHROOMS, DECKS, EXTENSIONS, NEW BUILDS,</p>
  </section>

  <section class="card card--front" aria-label="Card front">
    <div class="monogram-panel">
      <span class="monogram-panel__text">MP</span>
    </div>
    <div class="contact">
      <p class="contact__name">MARTIN POWLES</p>
      <p class="contact__role">Director</p>
      <p class="contact__row"><span><span class="label">Licence:</span> (527691K)</span><span class="contact__icon"></span></p>
      <p class="contact__row">0400382415
        <svg class="contact__icon" viewBox="0 0 24 24"><path d="M6.6 10.8a15.1 15.1 0 0 0 6.6 6.6l2.2-2.2c.3-.3.7-.4 1-.2 1.1.4 2.3.6 3.6.6.6 0 1 .4 1 1V20c0 .6-.4 1-1 1A17 17 0 0 1 3 4c0-.6.4-1 1-1h3.5c.6 0 1 .4 1 1 0 1.3.2 2.5.6 3.6.1.3 0 .7-.2 1z"/></svg>
      </p>
      <p class="contact__row">info@martinpowles.com
        <svg class="contact__icon" viewBox="0 0 24 24"><path d="M2 5h20v14H2z M4 7v.4l8 5 8-5V7z" fill-rule="evenodd"/></svg>
      </p>
      <p class="contact__row"><span>www.<span class="accent">martinpowles</span>.com</span>
        <svg class="contact__icon" viewBox="0 0 24 24"><circle cx="12" cy="12" r="10"/></svg>
      </p>
    </div>
  </section>

</body>
</html>
```